Front page on www.brightmarkgoods.com modern service ads - each ad for each featured service

We need to have initial 5 banners to be created for our soon to be launched new site,. These are 5 rotating banners that will showcase our companies key features. We are looking for a modern stylish yet simple look to highlight these features. Something thats very inviting and modern to fit the look of the new website.

5 banners need to be, information can be found on www.brightmarkgoods.com about these. Please ask if any questions

Why us?
Art Services
Order Process
Current promotions
Clearance products

please also note. the design will be going onto this website. http://new.brightmarkgoods.com/ Please base actual designs , color schemes etc.. for the new site.

Target Market(s)

Small businesses that purchase marketing promotional goods, to promote their business

Industry/Entity Type

Promotional Product

Font styles to use
Sans Serif

Requirements
Must have
• Size of the banner is 965 x 400 px
Nice to have
• Modern elements,, very clean and minimal look
Should not have
• no cheap generic clip art

```html
<!DOCTYPE html>
<html lang="en">
<head>
<meta charset="utf-8">
<title>Brightmark Goods – Current Promotions</title>
<link rel="stylesheet" href="https://fonts.googleapis.com/css2?family=Montserrat:ital,wght@1,800&family=Roboto+Condensed:wght@700&family=Hind:wght@400;600&display=swap">
<style>
  :root {
    --green: #5a9636;
    --blue: #4a78a6;
    --banner-bg: #e1e1e1;
    --page-bg: #ffffff;
    --content-bg: #dcdcdc;
    --text: #333333;
    --heading: #1f1f1f;
    --link: #3f6fa6;
    --white: #ffffff;
  }
  * { box-sizing: border-box; margin: 0; padding: 0; }
  html, body { width: 1200px; height: 800px; overflow: hidden; background: var(--page-bg); }
  .page { width: 1200px; height: 800px; display: flex; flex-direction: column; }

  .promo-banner { position: relative; width: 1200px; height: 500px; flex: none; }
  .banner-art {
    position: absolute; inset: 0;
    background: linear-gradient(90deg, var(--green) 0%, var(--banner-bg) 24%, var(--banner-bg) 76%, var(--green) 100%);
  }
  .corner { position: absolute; width: 34px; height: 34px; border: 0 solid var(--blue); }
  .corner-tl { left: 280px; top: 44px; border-top-width: 7px; border-left-width: 7px; }
  .corner-tr { left: 882px; top: 44px; border-top-width: 7px; border-right-width: 7px; }
  .corner-bl { left: 280px; top: 444px; border-bottom-width: 7px; border-left-width: 7px; }
  .corner-br { left: 882px; top: 444px; border-bottom-width: 7px; border-right-width: 7px; }

  .headline-panel {
    position: absolute; left: 335px; top: 132px; width: 462px; height: 222px;
    background: var(--green); border-radius: 0 30px 30px 0;
    display: flex; flex-direction: column; align-items: center; justify-content: center;
    color: var(--white); text-align: center;
  }
  .headline {
    font-family: "Montserrat", sans-serif; font-weight: 800; font-style: italic;
    font-size: 50px; line-height: 58px; letter-spacing: -0.5px;
  }
  .subline {
    font-family: "Roboto Condensed", sans-serif; font-weight: 700;
    font-size: 26px; line-height: 32px; margin-top: 4px;
  }
  .tag {
    position: absolute; left: 497px; top: 372px; width: 300px; height: 62px;
    background: var(--blue); border-radius: 4px;
    display: flex; flex-direction: column; align-items: center; justify-content: center;
    font-family: "Montserrat", sans-serif; font-weight: 800; font-style: italic;
    font-size: 22px; line-height: 28px; color: var(--white); text-align: center;
  }

  .welcome {
    flex: 1;
    background: var(--content-bg);
    padding: 18px 18px 0;
    font-family: "Hind", sans-serif;
    color: var(--text);
  }
  .welcome-title { font-weight: 600; font-size: 23px; color: var(--heading); margin-bottom: 14px; letter-spacing: -0.2px; }
  .welcome-text { font-size: 15px; line-height: 27px; margin-bottom: 10px; }
  .welcome-text a { color: var(--link); text-decoration: none; }
</style>
</head>
<body>
<main class="page">
  <section class="promo-banner">
    <div class="banner-art" role="img" aria-label="Abstract background of green and grey shapes"></div>
    <span class="corner corner-tl"></span>
    <span class="corner corner-tr"></span>
    <span class="corner corner-bl"></span>
    <span class="corner corner-br"></span>
    <div class="headline-panel">
      <h2 class="headline">CURRENT<br>PROMOTIONS</h2>
      <p class="subline">STELLAR DEALS STARTING FROM $1</p>
    </div>
    <p class="tag">DEALS THAT NO ONE<br>CAN RESIST</p>
  </section>

  <section class="welcome">
    <h1 class="welcome-title">Welcome to Brightmark Goods</h1>
    <p class="welcome-text">Your one stop shop for all your <a href="#">promotional product</a> needs. Here you will find everything you need to make your next promotion a huge success. Our endless list of <a href="#">promotional items</a> include <a href="#">custom calendars</a>, <a href="#">corporate gifts</a>, the newest in <a href="#">promotional tech items</a>, <a href="#">promotional tote bags</a>, <a href="#">custom pens</a> and so much more.</p>
    <p class="welcome-text">We took out all the guess work so you can purchase your <a href="#">promotional products</a> with tremendous ease. Our professional art department will strive to provide you with the best art work all at no extra cost. We will not stop until you are satisfied with your logo and are ready to proceed with production of your <a href="#">promotional items</a>.</p>
    <p class="welcome-text">We will not be beat, if you find an advertised price online; we will match it and in most cases beat it. We are confident that you will enjoy working with us. Our experience and determination will make your next promotion a wonderful success.</p>
  </section>
</main>
</body>
</html>
```